Plakat-Design für Softwareentwicklung im Automotive-Sektor
Zielgruppe
Softwareentwicklung im Automotive-Sektor
Aufgabenstellung
Guten Tag,
wir benötigen ein Design für die Standwände und die Infotheke (LED-beleuchtet) unseres Messestandes auf einer Automotive Fachmesse.
Druckdaten, ein Layout unseres Standes und alle weiteren nötigen Daten finden Sie im Upload.
Im Upload finden Sie auch unser Signature Bild, das in das Design eingearbeitet werden soll - beispielsweise auf der Rückwand und die Seitenwände werden mit Logo/Slogan/einfarbig passend gestaltet oder Sie binden das Bild ganz ein - wir sind offen und gespannt auf Ihre Vorschläge!)
Außerdem finden Sie im Upload unser Firmenlogo samt Slogan 'Build better systems.'
Unsere Website, um einen Eindruck vom Corporate Design zu erhalten:
https://www.quellorbit.de/de/
Wir freuen uns auf Ihre Designs!

```html
<!DOCTYPE html>
<html lang="de">
<head>
<meta charset="utf-8">
<title>QuellOrbit – Messestand Panels</title>
<link href="https://fonts.googleapis.com/css2?family=Open+Sans:wght@300;400;700;800&family=Oswald:wght@400;500&display=swap" rel="stylesheet">
<style>
  :root{
    --teal:#13877d;
    --panel:#4a4a4c;
    --panel-dark:#3f3f41;
    --white:#ffffff;
    --orange:#f0822a;
    --text-grey:#6d6e70;
    --photo-a:#4a4a4a;
    --photo-b:#161616;
  }
  *{box-sizing:border-box;margin:0;padding:0}
  html,body{width:1200px;height:3844px;overflow:hidden}
  body{
    position:relative;
    background:linear-gradient(180deg,#5c5d60 0%,#767779 35%,#8a8b8d 60%,#9b9c9e 100%);
    font-family:"Open Sans",sans-serif;
  }
  .panel{position:absolute;background:var(--panel);overflow:hidden}
  .teal-rule{position:absolute;left:0;top:0;width:100%;height:6px;background:var(--teal)}
  .header{position:absolute;left:0;width:100%;background:var(--white)}
  .brand{position:absolute;left:24px;display:flex;align-items:center;gap:12px}
  .brand-name{font-family:"Open Sans",sans-serif;font-weight:300;color:var(--teal);font-size:46px;letter-spacing:-1px;line-height:1}
  .brand-mark{width:30px;height:30px;background:var(--teal)}
  .brand-tagline{position:absolute;font-family:"Open Sans",sans-serif;font-weight:400;color:var(--text-grey);font-size:14px;white-space:nowrap}
  .brand.dark .brand-name{color:var(--panel)}
  .brand.dark .brand-mark{background:var(--panel)}
  .photo{position:absolute;left:0;width:100%;
    background:radial-gradient(ellipse 30% 70% at 60% 55%,rgba(200,110,40,.45),transparent 70%),linear-gradient(180deg,var(--photo-a) 0%,#2a2a2a 45%,var(--photo-b) 100%)}
  .url{position:absolute;left:0;width:100%;text-align:center;font-family:"Oswald",sans-serif;font-weight:400;color:var(--white);font-size:30px}
  .url.on-white{color:#333}
  .pattern{position:absolute;inset:0;background:linear-gradient(180deg,#474749,#424244)}
  .claim{font-family:"Oswald",sans-serif;font-weight:400;color:var(--orange);line-height:1}
  .claim span{display:block}
  .claim-box{position:absolute;left:27px;width:303px;height:320px;background:rgba(70,70,72,.85);padding:40px 0 0 27px}
  .claim-box .claim{font-size:56px}
  .claim-box .claim span{margin-bottom:28px}
  .services{position:absolute;left:0;width:100%;top:247px;text-align:center;color:var(--white);font-size:15px;line-height:21px}
  .services b{font-weight:800}
  .services .o{color:var(--orange)}
  .services .lg{font-size:18px}
  .column-text{position:absolute;top:30px;left:50%;transform-origin:0 0;transform:rotate(90deg) translateY(-50%);white-space:nowrap;
    font-family:"Open Sans",sans-serif;font-weight:300;font-size:50px;letter-spacing:-1px;display:flex;align-items:center;gap:14px}
  .column-text i{display:block;width:30px;height:30px}
</style>
</head>
<body>

<!-- Row 1 -->
<section class="panel" style="left:30px;top:57px;width:358px;height:900px">
  <div class="teal-rule"></div>
  <div class="header" style="top:6px;height:121px">
    <div class="brand" style="top:30px"><span class="brand-name">QuellOrbit</span><span class="brand-mark"></span></div>
    <div class="brand-tagline" style="left:32px;top:80px">Build better systems.</div>
  </div>
  <div class="photo" role="img" aria-label="Nachtaufnahme verschlungener Autobahnbrücken mit orangen Lichtspuren" style="top:127px;height:625px"></div>
  <div class="url" style="top:775px">www.quellorbit.de</div>
</section>

<section class="panel" style="left:413px;top:57px;width:358px;height:900px">
  <div class="teal-rule"></div>
  <div class="header" style="top:6px;height:121px">
    <div class="brand" style="top:30px"><span class="brand-name">QuellOrbit</span><span class="brand-mark"></span></div>
    <div class="brand-tagline" style="left:32px;top:80px">Build better systems.</div>
  </div>
  <div class="photo" role="img" aria-label="Nachtaufnahme verschlungener Autobahnbrücken mit orangen Lichtspuren" style="top:127px;height:625px"></div>
  <div class="url" style="top:775px">www.quellorbit.de</div>
</section>

<section class="panel" style="left:797px;top:57px;width:358px;height:900px">
  <div class="pattern" role="img" aria-label="Dezentes Flächenmuster in Grautönen"></div>
  <div class="url" style="top:420px">www.quellorbit.de</div>
</section>

<!-- Row 2 -->
<section class="panel" style="left:30px;top:991px;width:358px;height:899px">
  <div class="teal-rule"></div>
  <div class="header" style="top:6px;height:119px">
    <div class="url on-white" style="top:34px;font-size:36px">www.quellorbit.de</div>
  </div>
  <div class="photo" role="img" aria-label="Nachtaufnahme verschlungener Autobahnbrücken mit orangen Lichtspuren" style="top:125px;height:626px"></div>
</section>

<section class="panel" style="left:413px;top:991px;width:358px;height:899px">
  <div class="teal-rule"></div>
  <div class="header" style="top:6px;height:119px">
    <div class="brand" style="top:28px"><span class="brand-name">QuellOrbit</span><span class="brand-mark"></span></div>
    <div class="brand-tagline" style="left:26px;top:78px">Build better systems.</div>
  </div>
  <div class="photo" role="img" aria-label="Nachtaufnahme verschlungener Autobahnbrücken mit orangen Lichtspuren" style="top:125px;height:626px"></div>
  <div class="claim-box" style="top:282px"><div class="claim"><span>BUILD</span><span>BETTER</span><span>SYSTEMS</span></div></div>
</section>

<section class="panel" style="left:797px;top:991px;width:358px;height:899px">
  <div class="header" style="top:6px;height:117px">
    <div class="brand dark" style="top:28px;left:30px"><span class="brand-name">QuellOrbit</span><span class="brand-mark"></span></div>
    <div class="brand-tagline" style="left:36px;top:78px">Build better systems.</div>
  </div>
  <div class="services">
    APPLICATION <b class="o">SYSTEM DESIGN</b><br>
    HARDWARE DEVELOPMENT<br>
    <b>SIMULATION</b> <b class="o">QUALITY MANAGEMENT</b><br>
    <b class="lg">SOFTWARE DEVELOPMENT</b><br>
    <span class="o">REQUIREMENT ENGINEERING</span><br>
    <b>INTEGRATION</b> PROJEKT MANAGEMENT<br>
    <b class="o">VALIDATION / VERIFICATION</b><br>
    <b>EMBEDDED SYSTEMS</b>
  </div>
</section>

<!-- Row 3: counter front -->
<section class="panel" style="left:163px;top:1899px;width:462px;height:434px">
  <div class="teal-rule"></div>
  <div class="header" style="top:6px;height:74px">
    <div class="brand" style="top:14px;left:105px"><span class="brand-name" style="font-size:38px">QuellOrbit</span><span class="brand-mark" style="width:26px;height:26px"></span></div>
    <div class="brand-tagline" style="left:112px;top:54px;font-size:12px">Build better systems.</div>
  </div>
  <div class="photo" role="img" aria-label="Nachtaufnahme verschlungener Autobahnbrücken mit orangen Lichtspuren" style="top:80px;height:354px;width:300px"></div>
  <svg style="position:absolute;left:0;top:80px" width="462" height="354" viewBox="0 0 462 354">
    <path d="M240 0 C 330 80, 320 290, 170 354 L462 354 L462 0 Z" fill="var(--panel)"/>
    <path d="M240 0 C 330 80, 320 290, 170 354" fill="none" stroke="var(--orange)" stroke-width="8"/>
  </svg>
  <div class="claim" style="position:absolute;left:312px;top:120px;font-size:29px"><span style="margin-bottom:16px">BUILD</span><span style="margin-bottom:16px">BETTER</span><span>SYSTEMS</span></div>
</section>

<!-- Row 3: counter side -->
<section class="panel" style="left:163px;top:2366px;width:462px;height:430px">
  <div class="header" style="top:0;height:76px"></div>
  <div class="brand" style="top:132px;left:60px"><span class="brand-name" style="color:var(--white);font-size:52px">QuellOrbit</span><span class="brand-mark" style="background:var(--white)"></span></div>
  <div class="claim" style="position:absolute;left:137px;top:228px;font-size:29px;color:var(--white)"><span style="margin-bottom:16px">BUILD</span><span style="margin-bottom:16px">BETTER</span><span>SYSTEMS</span></div>
</section>

<!-- Row 3: columns -->
<section class="panel" style="left:661px;top:1899px;width:78px;height:897px;background:var(--white)">
  <div class="column-text" style="color:var(--panel)">QuellOrbit<i style="background:var(--panel)"></i></div>
</section>
<section class="panel" style="left:755px;top:1899px;width:78px;height:897px">
  <div class="column-text" style="color:var(--white)">QuellOrbit<i style="background:var(--white)"></i></div>
</section>

<!-- Row 3: small stand block -->
<section class="panel" style="left:845px;top:2424px;width:192px;height:372px;background:transparent">
  <div style="position:absolute;left:0;top:0;width:192px;height:61px;background:var(--white)"></div>
  <div style="position:absolute;left:0;top:66px;width:192px;height:235px;background:var(--panel)">
    <div style="position:absolute;left:76px;top:50px;width:40px;height:40px;background:var(--white)"></div>
    <div style="position:absolute;left:0;width:100%;top:120px;text-align:center;color:var(--white);font-weight:300;font-size:36px;line-height:34px">Quell<br>Orbit</div>
  </div>
  <div style="position:absolute;left:0;top:306px;width:192px;height:66px;background:var(--panel)"></div>
</section>

</body>
</html>
```